Corvane Paintless Dent Removal

Our company works on vehicles removing dents using a highly skilled trade which the metal is massaged out with special tools without disturbing the original paint, hence paintless dent removal. Besides keeping the paint and metal original its also very environmentally friendly since no paint or toxic fillers are used. Also we we are one of the most experienced companies in the business with 25 years

Target Market(s)

Retail Automobile consumers, Auto Dealerships and Auto Body Shops

Industry/Entity Type

Auto Repair

Contact Information for Business Card

Dale Hollister
PO Box 518 Brookmere, NY 11962
631-555-0148
corvanepdr@mailbox-example.com
website corvanepdr.example
youtube corvane paintless dent removal
25 years of experience removing Dents, Dings and Hail Damage

Font styles to use
Serif
Sans Serif

Colors

Designer to choose colors to be used in the design.

Requirements
Must have
• I do like things that are simple but classy and somewhat bold, also I like my logo so that should be somewhat important

```html
<!DOCTYPE html>
<html lang="en">
<head>
<meta charset="utf-8">
<title>Corvane Paintless Dent Removal – Business Card</title>
<link href="https://fonts.googleapis.com/css2?family=Roboto:wght@400;500;700;900&display=swap" rel="stylesheet">
<style>
  :root {
    --bg: #3b332e;
    --card: #1d1f21;
    --card-edge: #141516;
    --green: #6cc22b;
    --white: #f2f2f2;
    --silver: #8a8c8f;
    --gold: #d9a21b;
    --gold-dark: #8a6410;
  }
  * { margin: 0; padding: 0; box-sizing: border-box; }
  html, body {
    width: 1200px; height: 769px; overflow: hidden;
    background: var(--bg);
    font-family: "Roboto", Arial, sans-serif;
  }
  .canvas { position: relative; width: 1200px; height: 769px; }
  .card {
    position: absolute; width: 540px; height: 309px;
    background: var(--card);
    border-radius: 3px;
    box-shadow: 0 18px 40px rgba(0,0,0,.45);
  }
  .card--back { left: 50px; top: 80px; }
  .card--front { left: 610px; top: 380px; }

  /* back */
  .back-brand {
    position: absolute; left: 0; right: 0; top: 92px;
    display: flex; align-items: center; justify-content: center; gap: 12px;
  }
  .brand-dot {
    width: 18px; height: 18px; border-radius: 50%;
  }
  .back-brand .brand-dot { background: var(--silver); }
  .back-brand .brand-name {
    color: var(--silver); font-weight: 700; font-size: 26px; line-height: 1.05;
    letter-spacing: .5px; text-align: center;
  }
  .back-url {
    position: absolute; left: 0; right: 0; top: 212px;
    text-align: center; color: var(--silver);
    font-size: 14px; letter-spacing: 6px;
  }

  /* front */
  .front-brand {
    position: absolute; left: 26px; top: 104px; width: 215px;
    display: flex; align-items: center; gap: 10px;
  }
  .front-brand .brand-dot { background: var(--green); flex: none; }
  .front-brand .brand-name {
    color: var(--white); font-weight: 700; font-size: 21px; line-height: 1.1;
  }
  .divider {
    position: absolute; left: 258px; top: 52px; width: 1px; height: 190px;
    background: linear-gradient(to bottom, transparent, #cfcfcf 25%, #cfcfcf 75%, transparent);
  }
  .contact { position: absolute; left: 280px; top: 70px; color: var(--white); }
  .contact-name {
    color: var(--green); font-weight: 700; font-size: 21px;
    text-transform: uppercase; margin-bottom: 6px;
  }
  .contact-address { font-size: 14px; line-height: 1.35; margin-bottom: 8px; }
  .contact-list { list-style: none; font-size: 14px; line-height: 1.55; }
  .contact-list li { display: flex; align-items: center; gap: 8px; }
  .contact-list svg { width: 13px; height: 13px; flex: none; fill: var(--green); }
  .years-badge {
    position: absolute; right: 22px; top: 40px; width: 70px; height: 70px;
    border-radius: 50%;
    background: radial-gradient(circle, #f3c23a 0%, var(--gold) 55%, var(--gold-dark) 100%);
    display: flex; align-items: center; justify-content: center;
  }
  .years-badge-inner {
    width: 50px; height: 50px; border-radius: 50%; background: #111;
    display: flex; flex-direction: column; align-items: center; justify-content: center;
    color: var(--gold); line-height: 1;
  }
  .years-number { font-size: 20px; font-weight: 900; }
  .years-label { font-size: 8px; font-weight: 700; letter-spacing: .5px; }
</style>
</head>
<body>
<div class="canvas">

  <section class="card card--back">
    <div class="back-brand">
      <span class="brand-dot"></span>
      <span class="brand-name">Corvane<br>Paintless Dent Removal</span>
    </div>
    <div class="back-url">www.corvanepdr.example</div>
  </section>

  <section class="card card--front">
    <div class="front-brand">
      <span class="brand-dot"></span>
      <span class="brand-name">Corvane Paintless Dent Removal</span>
    </div>
    <div class="divider"></div>
    <div class="contact">
      <div class="contact-name">Dale Hollister</div>
      <div class="contact-address">PO Box 518<br>Brookmere, NY 11962</div>
      <ul class="contact-list">
        <li><svg viewBox="0 0 24 24"><path d="M6.6 10.8a15.1 15.1 0 0 0 6.6 6.6l2.2-2.2c.3-.3.7-.4 1-.2 1.1.4 2.3.6 3.6.6.6 0 1 .4 1 1V20c0 .6-.4 1-1 1A17 17 0 0 1 3 4c0-.6.4-1 1-1h3.5c.6 0 1 .4 1 1 0 1.3.2 2.5.6 3.6.1.3 0 .7-.2 1z"/></svg>631-555-0148</li>
        <li><svg viewBox="0 0 24 24"><path d="M2 5h20v14H2zM3.5 6.5 12 13l8.5-6.5z" fill-rule="evenodd"/></svg>corvanepdr@mailbox-example.com</li>
        <li><svg viewBox="0 0 24 24"><circle cx="12" cy="12" r="10"/></svg>corvanepdr.example</li>
        <li><svg viewBox="0 0 24 24"><rect x="2" y="4" width="20" height="16" rx="3"/></svg>corvane paintless dent removal</li>
      </ul>
    </div>
    <div class="years-badge" role="img" aria-label="25 years of experience removing dents, dings and hail damage">
      <div class="years-badge-inner">
        <span class="years-number">25</span>
        <span class="years-label">YEARS</span>
      </div>
    </div>
  </section>

</div>
</body>
</html>
```